Website Development for vaultmerrow.com.au

Build a new Wordpress/Responsive website for vaultmerrow.com.au

Target Market(s)

Compliance Managers, Risk Managers, Information Security and Cyber Security Professionals, Chief Data/Digital Officers, Chief Operating/Financial Officers, Business Continuity Professionals, Disaster Recovery Planners, Small Business Owners, Local/Federal Government entities

Industry/Entity Type

Data Service

Coding

Coded - Design and coding required

Number of Pages Required

5+ page

Font styles to use
Sans Serif

Colors

Designer to choose colors to be used in the design.

Requirements
Must have
• 1. Site Structure: Home Page plus the following chapter-pages for a) Services b) About c) Resources d) Blog e) Contact Us
• 2. Prefer site to built on wordpress and we can purchase a theme if needed (we currently use Kelp9 for other sites)
• 3. Blog needs to be wordpress based
• 4. We will host the site ourselves on our own servers
• 5. Responsive Design
Nice to have
• 1. Livechat capability/interface
• 2. Capability for marketing automation integration (such as hubspot, marketo, infusionsoft etc)
• 3. Capability for CRM integration (Salesforce)

```html
<!DOCTYPE html>
<html lang="en">
<head>
<meta charset="utf-8">
<title>Vaultmerrow – Because we care, we're security aware</title>
<link href="https://fonts.googleapis.com/css2?family=Roboto:wght@400;500;700;900&family=Mulish:wght@400;600;700&display=swap" rel="stylesheet">
<style>
:root{
  --blue:#1766c2;
  --blue-deep:#0c4f9f;
  --blue-dark:#0a3a78;
  --sky:#e8f1fb;
  --ink:#1f2226;
  --grey:#6b7076;
  --line:#d9dde2;
  --white:#ffffff;
  --footer:#1d1f22;
  --red:#e0493d;
}
*{box-sizing:border-box;margin:0;padding:0}
html,body{width:1200px;height:4433px;overflow:hidden;background:var(--white)}
body{font-family:'Mulish',sans-serif;color:var(--ink);position:relative}
.abs{position:absolute}
.brand{font-family:'Roboto',sans-serif;font-weight:700;color:var(--blue);display:flex;align-items:center;gap:10px}
.brand-dot{width:26px;height:26px;border-radius:50%;background:var(--blue)}

/* top bar */
.topbar{top:0;left:0;width:1200px;height:42px;font-size:14px;color:var(--grey)}
.topbar .item{position:absolute;top:12px;display:flex;align-items:center;gap:10px}
.socials{position:absolute;top:10px;left:860px;display:flex;align-items:center;gap:8px;font-size:14px;color:var(--ink)}
.socials span.sq{width:20px;height:20px;background:var(--red);border-radius:3px;display:inline-block}
.socials span.sq.b{background:var(--blue)}

/* nav */
.nav{top:42px;left:0;width:1200px;height:70px}
.nav .brand{position:absolute;left:140px;top:14px;font-size:34px}
.menu{position:absolute;left:0;top:0;width:1200px;height:70px;font-family:'Roboto',sans-serif;font-size:13px;font-weight:500;color:var(--ink)}
.menu a{position:absolute;top:36px;text-decoration:none;color:inherit;transform:translateX(-50%)}
.menu a.active{color:var(--blue)}
.menu a.active::after{content:"";position:absolute;left:-8px;right:-8px;top:-38px;height:4px;background:var(--blue)}
.menu a.active::before{content:"";position:absolute;left:-8px;right:-8px;bottom:-8px;height:2px;background:var(--blue)}

/* hero */
.hero{top:112px;left:0;width:1200px;height:620px}
.hero-photo{position:absolute;inset:0;background:linear-gradient(160deg,#2e4d78 0%,#4f7fb6 35%,#1d3558 70%,#0f1e36 100%)}
.hero h1{position:absolute;left:142px;top:128px;font-family:'Roboto',sans-serif;font-weight:700;font-size:52px;line-height:72px;color:var(--white)}
.btn-light{position:absolute;left:142px;top:281px;width:180px;height:44px;background:var(--white);color:var(--blue);font-family:'Roboto',sans-serif;font-weight:500;font-size:17px;display:flex;align-items:center;justify-content:center}
.hero svg{position:absolute;left:0;bottom:0}

/* about */
.about-photo{left:142px;top:763px;width:446px;height:446px;background:linear-gradient(135deg,#e3e9ef,#9fb1c4 55%,#5d6f86)}
.about-photo .brand{position:absolute;left:8px;top:8px;font-size:24px;color:var(--white)}
.about-head{left:632px;top:790px;font-family:'Roboto',sans-serif;font-size:36px;font-weight:500;color:var(--ink);display:flex;align-items:center;gap:18px}
.about-head .brand{font-size:42px}
.about-copy{left:632px;top:884px;width:430px;font-size:12.5px;line-height:19px;color:#444}
.about-copy p{margin-bottom:10px}
.about-copy b{color:var(--blue)}
.about-copy .cta{font-weight:700;color:var(--ink);font-size:14px}
.about-copy .cta span{color:var(--blue);font-weight:400}

/* services */
.services{top:1292px;left:0;width:1200px;height:570px;background:var(--sky)}
.section-title{position:absolute;left:0;width:1200px;text-align:center;font-family:'Roboto',sans-serif;font-weight:500;font-size:38px;color:var(--ink)}
.section-intro{position:absolute;left:200px;width:800px;text-align:center;font-size:12.5px;line-height:22px;color:#444}
.section-intro b{color:var(--blue);font-weight:400}
.svc-ring{position:absolute;width:112px;height:112px;border-radius:50%;border:6px solid #5f6368;background:var(--white);display:flex;align-items:center;justify-content:center}
.svc-ring.on{border-color:var(--blue)}
.svc-label{position:absolute;font-family:'Roboto',sans-serif;font-size:19px;line-height:27px;color:var(--ink)}
.svc-label.on{color:var(--blue)}
.svc-label.l{text-align:right}
.center-mark{position:absolute;left:497px;top:216px;width:206px;height:206px;border-radius:50%;background:var(--blue);display:flex;align-items:center;justify-content:center;color:var(--white);font-family:'Roboto',sans-serif;font-weight:700;font-size:24px}

/* audiences */
.serve{top:1862px;left:0;width:1200px;height:570px}
.aud{position:absolute;top:240px;width:144px;height:144px;border-radius:50%;background:var(--white);box-shadow:0 4px 14px rgba(0,0,0,.12);display:flex;align-items:center;justify-content:center}
.aud.on{border:6px solid var(--blue);box-shadow:0 0 0 6px var(--white),0 0 0 8px #b8cfe9}
.aud-label{position:absolute;top:410px;width:200px;text-align:center;font-size:17px;line-height:22px;color:#333}
.aud-label.on{color:var(--blue)}
.arrow{position:absolute;width:32px;height:32px;border-radius:50%;background:var(--white);box-shadow:0 2px 8px rgba(0,0,0,.15);display:flex;align-items:center;justify-content:center}

/* team */
.team{top:2433px;left:0;width:1200px;height:662px;background:linear-gradient(135deg,var(--blue-deep),var(--blue) 50%,var(--blue-deep))}
.team .section-title,.team .sub{color:var(--white)}
.team .sub{position:absolute;top:132px;width:1200px;text-align:center;font-size:22px}
.member{position:absolute;top:189px;width:192px;height:384px;background:var(--white);padding:16px}
.member.on{outline:4px solid #1c78de}
.member .pic{width:160px;height:207px;background:linear-gradient(180deg,#cbd5df,#8b9db0);border:6px solid #eef1f4;margin:0 auto}
.member h3{margin-top:20px;text-align:center;font-family:'Roboto',sans-serif;font-weight:400;font-size:16px;letter-spacing:.5px}
.member.on h3{color:var(--blue)}
.member .role{text-align:center;font-size:13px;color:var(--grey);margin-top:4px}
.member .icons{display:flex;justify-content:center;gap:8px;margin-top:12px}
.member .icons i{width:9px;height:9px;border-radius:50%;background:#8c9196;display:block}

/* blog */
.blog{top:3095px;left:0;width:1200px;height:645px;background:#edf3fa}
.post{position:absolute;top:195px;width:443px;height:266px;background:var(--white);box-shadow:0 4px 16px rgba(0,0,0,.08);border-bottom:5px solid var(--blue);text-align:center;padding:82px 40px 0}
.date{position:absolute;top:-56px;left:50%;transform:translateX(-50%);width:112px;height:112px;border-radius:50%;background:var(--white);border:7px solid #66696d;display:flex;flex-direction:column;align-items:center;justify-content:center}
.date b{font-family:'Roboto',sans-serif;font-size:40px;line-height:40px;color:var(--blue);font-weight:500}
.date span{font-size:12px;color:var(--blue)}
.post h3{font-family:'Roboto',sans-serif;font-size:17px;font-weight:500}
.post p{margin-top:14px;font-size:12.5px;line-height:19px;color:#555}
.post a{display:inline-block;margin-top:12px;font-size:13px;color:var(--blue);text-decoration:none;border-bottom:1px solid var(--blue)}
.btn-outline{position:absolute;left:526px;top:520px;width:148px;height:41px;border:2px solid var(--blue);color:var(--blue);display:flex;align-items:center;justify-content:center;font-size:15px;background:var(--white)}

/* contact */
.start{top:3740px;left:0;width:1200px;height:520px;background:linear-gradient(135deg,#1a5fae,#2a78cf 45%,#124b90)}
.start .section-title{color:var(--white);top:100px}
.form{position:absolute;left:313px;top:188px;width:642px;height:142px;border:1px solid rgba(255,255,255,.45);font-size:13px;color:rgba(255,255,255,.8)}
.form .f{position:absolute;left:0;width:320px;height:47px;border-bottom:1px solid rgba(255,255,255,.45);padding:14px 16px}
.form .f.first{background:#0d4b97}
.form .msg{position:absolute;left:320px;top:0;width:320px;height:140px;border-left:1px solid rgba(255,255,255,.45);padding:14px 24px}
.btn-submit{position:absolute;left:526px;top:360px;width:148px;height:36px;background:#c9ccd0;color:var(--white);font-family:'Roboto',sans-serif;font-weight:500;font-size:22px;display:flex;align-items:center;justify-content:center}

/* footer */
.footer{top:4200px;left:0;width:1200px;height:233px}
.footer svg{position:absolute;left:0;top:0}
.footer .brand{position:absolute;left:139px;top:96px;font-size:36px;color:var(--white)}
.footer .brand .brand-dot{background:var(--white)}
.fmenu{position:absolute;top:128px;left:0;width:1200px;font-family:'Roboto',sans-serif;font-size:13px;color:var(--white)}
.fmenu span{position:absolute;transform:translateX(-50%)}
.frule{position:absolute;left:139px;top:176px;width:922px;height:1px;background:#45484c}
.fcopy{position:absolute;top:197px;font-size:12px;color:#c7c9cc}
.chat{position:absolute;left:1018px;top:26px;width:48px;height:48px;border-radius:50%;background:var(--white);display:flex;align-items:center;justify-content:center}
</style>
</head>
<body>

<!-- top bar -->
<div class="abs topbar">
  <div class="item" style="left:139px">
    <svg width="14" height="14" viewBox="0 0 24 24"><path fill="#1766c2" d="M6.6 10.8a15 15 0 006.6 6.6l2.2-2.2a1 1 0 011-.25 11.4 11.4 0 003.6.6 1 1 0 011 1V20a1 1 0 01-1 1A17 17 0 013 4a1 1 0 011-1h3.5a1 1 0 011 1 11.4 11.4 0 00.6 3.6 1 1 0 01-.25 1z"/></svg>
    +61 3 9000 4127
  </div>
  <div class="item" style="left:290px">
    <svg width="16" height="12" viewBox="0 0 24 18"><rect width="24" height="18" rx="2" fill="#1766c2"/><path d="M2 2l10 8 10-8" stroke="#fff" stroke-width="2" fill="none"/></svg>
    info@vaultmerrow.com.au
  </div>
  <div class="socials">Follow Us on <span class="sq" style="margin-left:6px"></span><span class="sq b"></span><span class="sq b"></span><span class="sq"></span></div>
</div>

<!-- nav -->
<header class="abs nav">
  <div class="brand"><span class="brand-dot"></span>Vaultmerrow</div>
  <nav class="menu">
    <a class="active" style="left:550px">HOME</a>
    <a style="left:630px">ABOUT</a>
    <a style="left:718px">SERVICES</a>
    <a style="left:825px">RESOURCES</a>
    <a style="left:916px">BLOG</a>
    <a style="left:1010px">CONTACT US</a>
  </nav>
</header>

<!-- hero -->
<section class="abs hero">
  <div class="hero-photo" role="img" aria-label="Night aerial view of a city skyline with glowing network lines"></div>
  <h1>Because we care,<br>we're security aware</h1>
  <div class="btn-light">Contact Us Today</div>
  <svg width="1200" height="140" viewBox="0 0 1200 140" preserveAspectRatio="none">
    <path d="M0 70 C300 150 700 150 1000 60 C1100 30 1160 20 1200 22 L1200 140 L0 140Z" fill="#ffffff"/>
    <path d="M0 70 C300 150 700 150 1000 60 C1100 30 1160 20 1200 22" fill="none" stroke="#1766c2" stroke-width="4"/>
  </svg>
</section>

<!-- about -->
<div class="abs about-photo" role="img" aria-label="Smiling businessman in a suit working on a laptop in a bright office">
  <div class="brand">Vaultmerrow</div>
</div>
<h2 class="abs about-head">About <span class="brand"><span class="brand-dot"></span>Vaultmerrow</span></h2>
<div class="abs about-copy">
  <p><b>Vaultmerrow</b> It is a long established fact that a reader will be distracted by the readable content of a page when looking at its layout. The point of using Lorem Ipsum is that it has a more-or-less normal distribution</p>
  <p>The point of using Lorem Ipsum is that it has a more-or-less normal distribution of letters, as opposed to using 'Content here, content here', making it look like readable English</p>
  <p>Lorem Ipsum is that it has a more-or-less normal distribution of letters, as opposed to using 'Content here, content here', making it look like readable English has a more-or-less normal</p>
  <p>The point of using Lorem Ipsum is that it has a more-or-less normal distribution of letters, as opposed to using 'Content here, content here', making it look like readable English</p>
  <p class="cta">Get the support you need now. <span>Contact our 24/7 support line to get started.</span></p>
</div>

<!-- services -->
<section class="abs services">
  <h2 class="section-title" style="top:56px">SERVICES</h2>
  <p class="section-intro" style="top:128px"><b>Vaultmerrow</b> It is a long established fact that a reader will be distracted by the readable content of a page when looking at its layout.<br>The point of using Lorem Ipsum is that it has a more-or-less normal distribution of letters</p>
  <div class="center-mark">Vaultmerrow</div>

  <div class="svc-ring on" style="left:343px;top:218px">
    <svg width="44" height="44" viewBox="0 0 24 24" fill="none" stroke="#1766c2" stroke-width="1.6"><path d="M7 16a4 4 0 010-8 5 5 0 019.6 1.5A3.5 3.5 0 0117 16z"/><path d="M12 16v4M9 20h6"/></svg>
  </div>
  <div class="svc-ring" style="left:343px;top:374px">
    <svg width="44" height="44" viewBox="0 0 24 24" fill="none" stroke="#444" stroke-width="1.6"><ellipse cx="11" cy="5" rx="7" ry="2.5"/><path d="M4 5v12c0 1.4 3 2.5 7 2.5M18 5v6"/><path d="M4 11c0 1.4 3 2.5 7 2.5"/><circle cx="18" cy="17" r="3"/></svg>
  </div>
  <div class="svc-ring" style="left:742px;top:218px">
    <svg width="44" height="44" viewBox="0 0 24 24" fill="none" stroke="#444" stroke-width="1.6"><circle cx="9" cy="14" r="4"/><circle cx="17" cy="7" r="3"/><path d="M9 8v2M9 18v2M3 14h2M13 14h2"/></svg>
  </div>
  <div class="svc-ring" style="left:742px;top:374px">
    <svg width="44" height="44" viewBox="0 0 24 24" fill="none" stroke="#444" stroke-width="1.6"><rect x="3" y="4" width="18" height="14" rx="1"/><rect x="9" y="10" width="6" height="5"/><path d="M10 10V8a2 2 0 014 0v2"/></svg>
  </div>

  <div class="svc-label l on" style="left:95px;top:232px;width:230px">Data Management<br>Platforms</div>
  <div class="svc-label l" style="left:95px;top:390px;width:230px">Data Management<br>Services</div>
  <div class="svc-label" style="left:878px;top:232px">Industry<br>Solutions</div>
  <div class="svc-label" style="left:878px;top:390px">Ransomware<br>Protection</div>
</section>

<!-- audiences -->
<section class="abs serve">
  <h2 class="section-title" style="top:110px">TO WHOM WE SERVE</h2>
  <p class="section-intro" style="top:162px">The point of using Lorem Ipsum is that it has a more-or-less normal distribution of letters, as opposed to using 'Content here,<br>content here', making it look like readable English</p>

  <div class="arrow" style="left:76px;top:296px"><svg width="10" height="10" viewBox="0 0 10 10"><path d="M7 1L3 5l4 4" stroke="#666" stroke-width="1.6" fill="none"/></svg></div>
  <div class="arrow" style="left:1089px;top:296px"><svg width="10" height="10" viewBox="0 0 10 10"><path d="M3 1l4 4-4 4" stroke="#666" stroke-width="1.6" fill="none"/></svg></div>

  <div class="aud" style="left:141px"><svg width="56" height="56" viewBox="0 0 24 24" fill="none" stroke="#444" stroke-width="1.3"><path d="M10 3L2 19h16z"/><path d="M10 9v5M10 16v1"/><circle cx="18" cy="17" r="3.5"/></svg></div>
  <div class="aud" style="left:333px"><svg width="56" height="56" viewBox="0 0 24 24" fill="none" stroke="#444" stroke-width="1.3"><path d="M12 2l8 3v6c0 5-3.5 9-8 11-4.5-2-8-6-8-11V5z"/><path d="M8 12l3 3 5-6"/></svg></div>
  <div class="aud on" style="left:528px"><svg width="56" height="56" viewBox="0 0 24 24" fill="none" stroke="#1766c2" stroke-width="1.3"><rect x="5" y="5" width="14" height="14" rx="1"/><path d="M9 2v3M12 2v3M15 2v3M9 19v3M12 19v3M15 19v3M2 9h3M2 12h3M2 15h3M19 9h3M19 12h3M19 15h3"/><rect x="9.5" y="11" width="5" height="4"/><path d="M10.5 11V9.5a1.5 1.5 0 013 0V11"/></svg></div>
  <div class="aud" style="left:720px"><svg width="56" height="56" viewBox="0 0 24 24" fill="none" stroke="#444" stroke-width="1.3"><circle cx="12" cy="7" r="3"/><path d="M6 14h12v3H6zM4 17h16M8 20h8"/></svg></div>
  <div class="aud" style="left:912px"><svg width="56" height="56" viewBox="0 0 24 24" fill="none" stroke="#444" stroke-width="1.3"><circle cx="12" cy="7" r="4"/><path d="M4 21c0-4.5 3.6-7 8-7s8 2.5 8 7z"/><path d="M12 14v7"/></svg></div>

  <div class="aud-label" style="left:113px">Risk Managers</div>
  <div class="aud-label" style="left:305px">Information<br>Security</div>
  <div class="aud-label on" style="left:500px">Cyber Security<br>Professionals</div>
  <div class="aud-label" style="left:692px">Chief Data<br>Technicians</div>
  <div class="aud-label" style="left:884px">Digital Officers</div>
</section>

<!-- team -->
<section class="abs team">
  <h2 class="section-title" style="top:82px">OUR TEAM</h2>
  <div class="sub">Our Bestest Team Members.</div>

  <div class="arrow" style="left:138px;top:344px"><svg width="10" height="10" viewBox="0 0 10 10"><path d="M7 1L3 5l4 4" stroke="#333" stroke-width="1.8" fill="none"/></svg></div>
  <div class="arrow" style="left:1021px;top:344px"><svg width="10" height="10" viewBox="0 0 10 10"><path d="M3 1l4 4-4 4" stroke="#333" stroke-width="1.8" fill="none"/></svg></div>

  <div class="member" style="left:189px"><div class="pic" role="img" aria-label="Portrait of a team member"></div><h3>MARLO</h3><div class="role">Designation Here</div><div class="icons"><i></i><i></i><i></i><i></i></div></div>
  <div class="member on" style="left:408px"><div class="pic" role="img" aria-label="Portrait of a team member"></div><h3>TESSA WARD</h3><div class="role">Designation Here</div><div class="icons"><i></i><i></i><i></i><i></i></div></div>
  <div class="member" style="left:624px"><div class="pic" role="img" aria-label="Portrait of a team member"></div><h3>OWEN HALE</h3><div class="role">Designation Here</div><div class="icons"><i></i><i></i><i></i><i></i></div></div>
  <div class="member" style="left:840px"><div class="pic" role="img" aria-label="Portrait of a team member"></div><h3>RAVI LUND</h3><div class="role">Designation Here</div><div class="icons"><i></i><i></i><i></i><i></i></div></div>
</section>

<!-- blog -->
<section class="abs blog">
  <h2 class="section-title" style="top:66px">LATEST BLOG POSTS</h2>

  <div class="arrow" style="left:87px;top:312px"><svg width="10" height="10" viewBox="0 0 10 10"><path d="M7 1L3 5l4 4" stroke="#666" stroke-width="1.6" fill="none"/></svg></div>
  <div class="arrow" style="left:1078px;top:312px"><svg width="10" height="10" viewBox="0 0 10 10"><path d="M3 1l4 4-4 4" stroke="#666" stroke-width="1.6" fill="none"/></svg></div>

  <article class="post" style="left:142px">
    <div class="date"><b>12</b><span>Feb 2019</span></div>
    <h3>The point of using Lorem Ipsum</h3>
    <p>"The point of using Lorem Ipsum is that it has a more-or-less normal distribution of letters, as opposed to using 'Content here, content here', making it look like readable English etters, as opposed to using 'Content here, content here'.</p>
    <a>Learn More</a>
  </article>
  <article class="post" style="left:615px">
    <div class="date"><b>06</b><span>Feb 2019</span></div>
    <h3>The point of using Lorem Ipsum</h3>
    <p>"The point of using Lorem Ipsum is that it has a more-or-less normal distribution of letters, as opposed to using 'Content here, content here', making it look like readable English etters, as opposed to using 'Content here, content here'.</p>
    <a>Learn More</a>
  </article>

  <div class="btn-outline">View All</div>
</section>

<!-- contact -->
<section class="abs start" role="img" aria-label="Blue tinted photo of people working at laptops">
  <h2 class="section-title">LET'S GET STARTED</h2>
  <div class="form">
    <div class="f first" style="top:0">Your Name</div>
    <div class="f" style="top:47px">Your Email</div>
    <div class="f" style="top:94px;border-bottom:none">Your Contact Number</div>
    <div class="msg">Your Message</div>
  </div>
  <div class="btn-submit">Submit</div>
</section>

<!-- footer -->
<footer class="abs footer">
  <svg width="1200" height="233" viewBox="0 0 1200 233" preserveAspectRatio="none">
    <path d="M0 60 C300 0 900 0 1200 60 L1200 233 L0 233Z" fill="#1d1f22"/>
  </svg>
  <div class="chat"><svg width="26" height="26" viewBox="0 0 24 24"><path fill="#1766c2" d="M4 4h16v11H9l-5 4z"/></svg></div>
  <div class="brand"><span class="brand-dot"></span>Vaultmerrow</div>
  <nav class="fmenu">
    <span style="left:550px">HOME</span>
    <span style="left:630px">ABOUT</span>
    <span style="left:718px">SERVICES</span>
    <span style="left:825px">RESOURCES</span>
    <span style="left:916px">BLOG</span>
    <span style="left:1010px">CONTACT US</span>
  </nav>
  <div class="frule"></div>
  <div class="fcopy" style="left:139px">Copyright 2019 @ Vaultmerrow. All Rights Reserved.</div>
  <div class="fcopy" style="left:877px">Terms of services / Privacy Policy</div>
</footer>

</body>
</html>
```